Trade Show Marlow 3x3 booth schel scheme

We would like to have full coverage design for 3x3 booth scheel

2x2 pop up Counter (1200mm wide x 900mm high x 400mm deep)
Our company provides food safety training, consultancy and food safety app service for hospitality businesses.

```html
<!DOCTYPE html>
<html lang="en">
<head>
<meta charset="utf-8">
<title>Caldwyn – Booth Graphics</title>
<link rel="stylesheet" href="https://fonts.googleapis.com/css2?family=Anton&family=Oswald:wght@300;500&family=Great+Vibes&display=swap">
<style>
  :root {
    --canvas: #eceff3;
    --cream: #fcfce1;
    --cream-deep: #f4f5d2;
    --lime: #cbd52f;
    --leaf: #97b532;
    --leaf-dark: #5d8c12;
    --ink: #1b1b1b;
    --charcoal: #2a2a2a;
    --orange: #f6a03c;
    --carrot: #f08a3a;
    --text-light: #fdfdeb;
  }
  * { margin: 0; padding: 0; box-sizing: border-box; }
  html, body { width: 1200px; height: 905px; overflow: hidden; background: var(--canvas); }
  .canvas { position: relative; width: 1200px; height: 905px; }

  .panel { position: absolute; overflow: hidden; }
  .panel-peace { left: 53px; top: 55px; width: 534px; height: 440px; background: var(--cream); }
  .panel-rating { left: 614px; top: 54px; width: 534px; height: 440px; background: var(--cream); }
  .panel-banner { left: 258px; top: 542px; width: 685px; height: 300px; background: var(--charcoal); }

  .panel-shape { position: absolute; inset: 0; width: 100%; height: 100%; }
  .art { position: absolute; border-radius: 18px; }
  .dot { position: absolute; border-radius: 50%; }

  .headline { position: absolute; font-family: "Anton", "Oswald", sans-serif; text-transform: uppercase; line-height: 1; white-space: nowrap; }
  .lead-in { position: absolute; font-family: "Oswald", sans-serif; font-weight: 300; color: var(--text-light); white-space: nowrap; line-height: 1; }
  .script { position: absolute; font-family: "Great Vibes", cursive; color: var(--ink); white-space: nowrap; line-height: 1; }
  .wordmark { position: absolute; font-family: "Oswald", sans-serif; font-weight: 500; letter-spacing: 0.4em; line-height: 1; white-space: nowrap; }

  /* Panel 1 */
  .peace-lead { left: 226px; top: 30px; font-size: 41px; letter-spacing: -0.02em; }
  .peace-title { left: 224px; top: 76px; font-size: 80px; color: var(--text-light); letter-spacing: -0.01em; line-height: 0.98; }
  .peace-title .bang { color: var(--leaf-dark); display: inline-block; transform: skewX(-8deg); }
  .peace-mark { left: 271px; top: 370px; font-size: 38px; color: var(--ink); }
  .art-produce { left: 28px; top: 89px; width: 160px; height: 192px; background: linear-gradient(160deg, #f7a35a 0%, var(--carrot) 45%, #f8bd85 100%); }
  .art-leaf-1 { left: 411px; top: 222px; width: 112px; height: 114px; background: linear-gradient(140deg, var(--leaf-dark) 0%, var(--leaf) 45%, var(--lime) 100%); }

  /* Panel 2 */
  .rating-script { left: 212px; top: 22px; font-size: 40px; }
  .rating-title { left: 214px; top: 82px; font-size: 68px; color: var(--text-light); line-height: 0.85; }
  .rating-sub { left: 214px; top: 260px; font-size: 50px; color: var(--ink); line-height: 0.9; letter-spacing: -0.01em; }
  .art-plate { left: 10px; top: 36px; width: 187px; height: 151px; background: linear-gradient(135deg, var(--cream-deep) 0%, #e3e5bf 50%, var(--leaf) 100%); }
  .art-leaf-2 { left: 29px; top: 266px; width: 152px; height: 141px; background: linear-gradient(140deg, var(--leaf-dark) 0%, var(--leaf) 45%, var(--lime) 100%); }

  /* Panel 3 */
  .banner-mark { left: 0; right: 0; top: 114px; text-align: center; font-size: 52px; color: var(--text-light); padding-left: 0.4em; }
  .banner-lines { left: 0; right: 0; top: 186px; text-align: center; font-size: 40px; color: var(--text-light); line-height: 1.02; letter-spacing: -0.01em; padding-left: 16px; }
  .banner-lines .accent { color: var(--lime); }
  .art-leaf-3 { left: 173px; top: 0; width: 117px; height: 82px; border-radius: 0 0 18px 18px; background: linear-gradient(140deg, var(--leaf-dark) 0%, var(--leaf) 45%, var(--lime) 100%); }
  .art-avocado { left: 157px; top: 209px; width: 56px; height: 76px; border-radius: 14px; background: linear-gradient(160deg, var(--leaf-dark) 0%, var(--leaf) 55%, #d9e07a 100%); }
</style>
</head>
<body>
<main class="canvas">

  <section class="panel panel-peace">
    <svg class="panel-shape" viewBox="0 0 984 811" preserveAspectRatio="none" aria-hidden="true">
      <path fill="var(--lime)" d="M350,0 L984,0 L984,380 C950,520 850,615 700,615 C520,615 400,500 380,390 C300,380 220,320 220,240 C220,150 290,100 350,100 C340,60 345,20 350,0 Z"/>
    </svg>
    <div class="art art-produce" role="img" aria-label="Illustration of a carrot and bread loaf with a tick badge"></div>
    <div class="art art-leaf-1" role="img" aria-label="Illustration of spinach leaves"></div>
    <span class="dot" style="left:75px;top:27px;width:8px;height:8px;background:var(--orange)"></span>
    <span class="dot" style="left:110px;top:21px;width:8px;height:8px;background:var(--orange)"></span>
    <span class="dot" style="left:106px;top:51px;width:8px;height:8px;background:var(--orange)"></span>
    <span class="dot" style="left:101px;top:29px;width:5px;height:5px;background:var(--lime)"></span>
    <span class="dot" style="left:90px;top:46px;width:5px;height:5px;background:var(--lime)"></span>
    <span class="dot" style="left:98px;top:322px;width:14px;height:14px;background:var(--orange)"></span>
    <span class="dot" style="left:139px;top:351px;width:14px;height:14px;background:var(--orange)"></span>
    <span class="dot" style="left:81px;top:378px;width:14px;height:14px;background:var(--orange)"></span>
    <span class="dot" style="left:102px;top:348px;width:8px;height:8px;background:var(--lime)"></span>
    <span class="dot" style="left:117px;top:376px;width:8px;height:8px;background:var(--lime)"></span>
    <p class="lead-in peace-lead">Our Promise Is</p>
    <h2 class="headline peace-title">Peace of<br>Mind<span class="bang">!</span></h2>
    <p class="wordmark peace-mark">CALDWYN</p>
  </section>

  <section class="panel panel-rating">
    <svg class="panel-shape" viewBox="0 0 985 811" preserveAspectRatio="none" aria-hidden="true">
      <path fill="var(--lime)" d="M380,0 H985 V580 C900,660 760,690 700,720 C640,760 560,775 500,770 C380,760 250,680 250,520 C250,420 300,380 290,330 C280,280 330,150 380,0 Z"/>
    </svg>
    <div class="art art-plate" role="img" aria-label="Illustration of a plate with fork, knife, salad and a tick badge"></div>
    <div class="art art-leaf-2" role="img" aria-label="Illustration of spinach leaves"></div>
    <p class="script rating-script">Achieve &amp; Maintain</p>
    <h2 class="headline rating-title">5 Star<br>Hygiene<br>Rating</h2>
    <p class="headline rating-sub">With Experts<br>At Your Side</p>
  </section>

  <section class="panel panel-banner">
    <div class="art art-leaf-3" role="img" aria-label="Illustration of spinach leaves"></div>
    <div class="art art-avocado" role="img" aria-label="Illustration of a halved avocado with a tick badge"></div>
    <span class="dot" style="left:455px;top:46px;width:13px;height:13px;background:var(--lime)"></span>
    <span class="dot" style="left:496px;top:43px;width:13px;height:13px;background:var(--lime)"></span>
    <span class="dot" style="left:502px;top:75px;width:13px;height:13px;background:var(--lime)"></span>
    <span class="dot" style="left:485px;top:272px;width:12px;height:12px;background:var(--orange)"></span>
    <span class="dot" style="left:480px;top:292px;width:7px;height:7px;background:var(--lime)"></span>
    <p class="wordmark banner-mark">CALDWYN</p>
    <h2 class="headline banner-lines">Food <span class="accent">Hygiene</span><br><span class="accent">Health</span> Safety</h2>
  </section>

</main>
</body>
</html>
```